Phuket Thailand - Rental Villa Website

I have a villa for rent in Thailand and require a website - i need to demo pictures/walk through video, local attractions, villa facilities description plus seaonal rates and online booking.

Industry/Entity Type

Rental

Coding

Coded - Design and coding required

```html
<!DOCTYPE html>
<html lang="en">
<head>
<meta charset="utf-8">
<title>Palm Cove Villas</title>
<link href="https://fonts.googleapis.com/css2?family=Open+Sans:wght@400;600;700&family=Kaushan+Script&display=swap" rel="stylesheet">
<style>
:root{
  --blue:#2a86c6;
  --blue-dark:#1b74b4;
  --blue-light:#45a9e0;
  --orange:#f47c20;
  --orange-dark:#e2660c;
  --text:#6b6b6b;
  --line:#e3e3e3;
  --footer:#f4f4f4;
  --bar:#e9e9e9;
}
*{box-sizing:border-box;margin:0;padding:0}
html,body{width:711px;height:1200px;overflow:hidden;background:#fff}
body{font-family:"Open Sans",Arial,sans-serif;color:var(--text);position:relative}
.abs{position:absolute}
.topline{left:0;top:0;width:711px;height:3px;background:var(--blue)}
.header{left:0;top:3px;width:711px;height:62px;background:linear-gradient(#fbfbfb,#fff)}
.brand{left:58px;top:25px;font-size:17px;font-weight:400;color:#666;display:flex;align-items:center;gap:8px}
.brand i{width:12px;height:12px;background:var(--orange);border-radius:50%;display:block}
.contact-item{top:29px;display:flex;align-items:center;gap:5px;font-size:6.4px;color:#777}
.contact-item b{font-weight:400;color:var(--blue)}
.ico{width:19px;height:19px;border-radius:50%;background:var(--orange);display:flex;align-items:center;justify-content:center}
.nav{left:0;top:65px;width:711px;height:23px;background:linear-gradient(var(--blue-light),var(--blue-dark));border-top:1px solid #7cc3ea}
.nav a{position:absolute;top:0;height:22px;line-height:22px;text-align:center;font-size:6.4px;color:#fff;text-decoration:none;border-right:1px solid rgba(0,0,0,.12);text-transform:uppercase}
.nav a.active{background:linear-gradient(#fa9a3f,var(--orange-dark))}
.hero{left:58px;top:100px;width:595px;height:211px;background:linear-gradient(180deg,#a9b6c4 0%,#6f8190 35%,#4f5a52 60%,#8b8a86 80%,#3b3b3b 100%);overflow:hidden}
.hero-title{left:26px;top:40px;font-family:"Kaushan Script",cursive;font-size:19px;line-height:22px;color:#fff;text-shadow:0 1px 3px rgba(0,0,0,.5)}
.hero-caption{left:0;top:176px;width:595px;height:35px;background:rgba(0,0,0,.55);color:#fff;font-size:8.6px;line-height:35px;padding-left:16px}
.pager{display:flex;gap:2px}
.pager span{width:11px;height:12px;background:#ddd;display:flex;align-items:center;justify-content:center}
.hero .pager{position:absolute;right:12px;top:187px}
.hero .pager span{background:rgba(255,255,255,.15)}
h2{font-size:8.2px;font-weight:700;color:var(--blue);text-transform:uppercase}
.intro{left:58px;top:349px;width:595px;font-size:6px;line-height:14.5px;color:var(--text)}
.rule{height:1px;background:var(--line)}
.card{top:441px;width:110px}
.card .photo{height:78px;border-radius:2px}
.card .meta{display:flex;justify-content:space-between;align-items:center;margin-top:6px;font-size:7px;color:var(--blue)}
.card .meta small{font-size:5px;color:#888}
.card .meta em{font-style:normal;color:var(--orange);letter-spacing:.5px}
.pin{font-size:6.3px;color:#777;margin-top:4px;display:flex;align-items:center;gap:3px}
.card .specs{border-top:1px solid var(--line);margin-top:4px;padding-top:5px;font-size:5.9px;line-height:11.3px;color:var(--blue)}
.btn{display:block;width:60px;height:17px;margin-top:6px;background:linear-gradient(#f98f30,var(--orange-dark));color:#fff;font-size:5.4px;font-weight:700;text-align:center;line-height:17px;border-radius:2px}
.video{left:58px;top:653px;width:229px;height:155px;border:1px solid #ccc}
.video .screen{height:144px;background:linear-gradient(180deg,#8fb6dc 0%,#4e86b2 40%,#3c6a7e 65%,#2b2a28 100%)}
.video .bar{height:10px;background:#e6e6e6;display:flex;align-items:center;gap:4px;padding:0 4px;font-size:4.5px;color:#333}
.video .track{flex:1;height:3px;background:#999}
.news{left:318px;width:335px;display:flex;gap:15px}
.news .thumb{width:88px;height:59px;flex:none}
.news h3{font-size:7.4px;font-weight:400;color:var(--blue)}
.news .date{font-size:5.9px;color:var(--orange);margin-top:6px}
.news p{font-size:5.9px;line-height:14px;margin-top:5px;color:#777}
.tab{top:834px;height:24px;line-height:24px;text-align:center;color:#fff;font-size:6.6px;font-weight:600;text-transform:uppercase}
.panel{left:58px;top:858px;width:595px;height:138px;border:1px solid #ddd;background:#fafafa}
.villa{top:872px;width:104px;height:109px;background:#fff;border:1px solid #e2e2e2;border-radius:2px;padding:4px}
.villa .photo{height:68px}
.villa h4{font-size:6.2px;font-weight:400;color:var(--blue);margin:7px 0 0 5px}
.villa .pin{margin:5px 0 0 5px}
.footer{left:0;top:1014px;width:711px;height:158px;background:var(--footer)}
.fcol{top:1034px;font-family:Arial,sans-serif}
.fcol h5{font-family:"Open Sans",Arial,sans-serif;font-size:6.4px;font-weight:700;color:var(--blue);margin-bottom:6px}
.fcol li{list-style:none;font-size:5.9px;line-height:14.2px;color:#555}
.fcol .strong{color:var(--blue-dark)}
.social li{display:flex;align-items:center;gap:4px;line-height:20.8px}
.social i{width:15px;height:15px;border-radius:50%;display:block}
.flogo{left:566px;top:1078px;font-size:12px;color:#777}
.copy{left:0;top:1172px;width:711px;height:28px;background:var(--bar);text-align:center;line-height:28px;font-size:5.6px;color:#555;font-family:Arial,sans-serif}
</style>
</head>
<body>
<div class="abs topline"></div>
<header class="abs header"></header>
<div class="abs brand"><i></i>Palm Cove Villas</div>
<div class="abs contact-item" style="left:398px">
  <span class="ico"><svg width="9" height="9" viewBox="0 0 24 24"><path fill="#fff" d="M6.6 10.8a15 15 0 006.6 6.6l2.2-2.2c.3-.3.7-.4 1-.2 1.1.4 2.3.6 3.6.6.6 0 1 .4 1 1V20c0 .6-.4 1-1 1A17 17 0 013 4c0-.6.4-1 1-1h3.5c.6 0 1 .4 1 1 0 1.3.2 2.5.6 3.6.1.3 0 .7-.2 1z"/></svg></span>
  CALL US : <b>(3652) 410 872</b>
</div>
<div class="abs contact-item" style="left:511px">
  <span class="ico"><svg width="9" height="9" viewBox="0 0 24 24"><path fill="#fff" d="M2 5h20v14H2z"/><path d="M2 5l10 8 10-8" stroke="#f47c20" stroke-width="2" fill="none"/></svg></span>
  EMAIL US : <b>info@palmcovevillas.com</b>
</div>

<nav class="abs nav">
  <a class="active" style="left:60px;width:56px">Home</a>
  <a style="left:116px;width:78px">About us</a>
  <a style="left:194px;width:69px">Services</a>
  <a style="left:263px;width:63px">Villas</a>
  <a style="left:326px;width:66px">Videos</a>
  <a style="left:392px;width:70px">Gallery</a>
  <a style="left:462px;width:58px">News</a>
  <a style="left:520px;width:82px">Contact us</a>
</nav>

<section class="abs hero" role="img" aria-label="Villa terrace with lounge sofas overlooking a mountain lake">
  <div class="abs hero-title">Palm Cove Villas in Phuket,<br>it is in Thailand.</div>
  <div class="abs hero-caption">LOREM IPSUM HAS BEEN THE INDUSTRY'S STANDARD DUMMY TEXT EVER SINCE THE 1500S, WHEN AN UNKNOWN...</div>
  <div class="pager"><span><svg width="4" height="6"><path d="M4 0L0 3l4 3" fill="#ccc"/></svg></span><span><svg width="4" height="6"><path d="M0 0l4 3-4 3" fill="#ccc"/></svg></span></div>
</section>

<h2 class="abs" style="left:58px;top:333px">Welcome to Palm Cove Villas</h2>
<p class="abs intro">Lorem Ipsum is simply dummy text of the printing and typesetting industry. Lorem Ipsum has been the industry's standard dummy text ever since the 1500s, when an unknown printer took a galley of type and scrambled it to make a type specimen book. It has survived not only five centuries, but also the leap into electronic typesetting, remaining essentially unchanged. It was popularised in the 1960s with the release of Letraset sheets containing...</p>

<h2 class="abs" style="left:58px;top:409px">Local Attractions</h2>
<div class="abs pager" style="left:630px;top:412px"><span></span><span></span></div>
<div class="abs rule" style="left:58px;top:429px;width:595px"></div>

<article class="abs card" style="left:58px">
  <div class="photo" role="img" aria-label="Villa bedroom interior" style="background:linear-gradient(135deg,#5a4a42,#a8a19a 60%,#d8d8dc)"></div>
  <div class="meta">Facility<small>Rated <em>★★★★☆</em></small></div>
  <div class="pin"><svg width="5" height="7" viewBox="0 0 10 14"><path d="M5 0a5 5 0 00-5 5c0 4 5 9 5 9s5-5 5-9a5 5 0 00-5-5z" fill="#777"/></svg>lorem ipsum</div>
  <div class="specs">2 Bed Rooms,<br>2 Attached Bathrooms,<br>Swimming pool</div>
  <span class="btn">BUY NOW</span>
</article>
<article class="abs card" style="left:180px">
  <div class="photo" role="img" aria-label="Covered pavilion beside an infinity pool" style="background:linear-gradient(180deg,#9aa7b2,#5a4436 45%,#b8c0c0)"></div>
  <div class="meta">Facility<small>Rated <em>★★★★☆</em></small></div>
  <div class="pin"><svg width="5" height="7" viewBox="0 0 10 14"><path d="M5 0a5 5 0 00-5 5c0 4 5 9 5 9s5-5 5-9a5 5 0 00-5-5z" fill="#777"/></svg>lorem ipsum</div>
  <div class="specs">2 Bed Rooms,<br>2 Attached Bathrooms,<br>Swimming pool</div>
  <span class="btn">BUY NOW</span>
</article>
<article class="abs card" style="left:302px">
  <div class="photo" role="img" aria-label="Villa roof among tropical garden" style="background:linear-gradient(135deg,#4f6a3a,#6e5a4e 55%,#8f8a80)"></div>
  <div class="meta">Facility<small>Rated <em>★★★★☆</em></small></div>
  <div class="pin"><svg width="5" height="7" viewBox="0 0 10 14"><path d="M5 0a5 5 0 00-5 5c0 4 5 9 5 9s5-5 5-9a5 5 0 00-5-5z" fill="#777"/></svg>lorem ipsum</div>
  <div class="specs">2 Bed Rooms,<br>2 Attached Bathrooms,<br>Swimming pool</div>
  <span class="btn">BUY NOW</span>
</article>
<article class="abs card" style="left:422px">
  <div class="photo" role="img" aria-label="Timber pavilion terrace with sea view" style="background:linear-gradient(180deg,#7a5a44,#4a3a30 50%,#6a7a70)"></div>
  <div class="meta">Facility<small>Rated <em>★★★★☆</em></small></div>
  <div class="pin"><svg width="5" height="7" viewBox="0 0 10 14"><path d="M5 0a5 5 0 00-5 5c0 4 5 9 5 9s5-5 5-9a5 5 0 00-5-5z" fill="#777"/></svg>lorem ipsum</div>
  <div class="specs">2 Bed Rooms,<br>2 Attached Bathrooms,<br>Swimming pool</div>
  <span class="btn">BUY NOW</span>
</article>
<article class="abs card" style="left:543px">
  <div class="photo" role="img" aria-label="Infinity pool overlooking a lake" style="background:linear-gradient(180deg,#b4bcc2,#8b9a94 40%,#5f8a86)"></div>
  <div class="meta">Facility<small>Rated <em>★★★★☆</em></small></div>
  <div class="pin"><svg width="5" height="7" viewBox="0 0 10 14"><path d="M5 0a5 5 0 00-5 5c0 4 5 9 5 9s5-5 5-9a5 5 0 00-5-5z" fill="#777"/></svg>lorem ipsum</div>
  <div class="specs">2 Bed Rooms,<br>2 Attached Bathrooms,<br>Swimming pool</div>
  <span class="btn">BUY NOW</span>
</article>

<div class="abs video">
  <div class="screen" role="img" aria-label="Villa walkthrough video: beach terrace with sea view" style="display:flex;align-items:center;justify-content:center">
    <svg width="34" height="34" viewBox="0 0 34 34"><circle cx="17" cy="17" r="15" fill="rgba(255,255,255,.15)" stroke="#fff" stroke-width="2.5"/><path d="M13 10l11 7-11 7z" fill="#fff"/></svg>
  </div>
  <div class="bar"><svg width="5" height="5"><path d="M0 0l5 2.5L0 5z" fill="#111"/></svg>00:00<span class="track"></span>00:00<svg width="10" height="5"><path d="M0 1h2l3-1v5L2 4H0z" fill="#333"/></svg></div>
</div>

<h2 class="abs" style="left:318px;top:651px">Latest News</h2>
<div class="abs pager" style="left:630px;top:650px"><span></span><span></span></div>

<article class="abs news" style="top:673px">
  <div class="thumb" role="img" aria-label="Villa with lit pool at dusk" style="background:linear-gradient(180deg,#1f4f8f,#3b79c0 50%,#0d2a55)"></div>
  <div>
    <h3>Lorem Ipsum is simply dummy text of the printing.</h3>
    <div class="date">Posted on 27 January 2015</div>
    <p>Lorem Ipsum is simply dummy text of the printing and typesetting industry. Lorem Ipsum has been the industry's...</p>
  </div>
</article>
<article class="abs news" style="top:748px">
  <div class="thumb" role="img" aria-label="Happy family on holiday" style="background:linear-gradient(135deg,#e9e4dc,#c9a68a 55%,#eef0f2)"></div>
  <div>
    <h3>Lorem Ipsum is simply dummy text of the printing.</h3>
    <div class="date">Posted on 27 January 2015</div>
    <p>Lorem Ipsum is simply dummy text of the printing and typesetting industry. Lorem Ipsum has been the industry's...</p>
  </div>
</article>

<div class="abs tab" style="left:58px;width:94px;background:linear-gradient(#fa9a3f,var(--orange-dark))">Recent Villas</div>
<div class="abs tab" style="left:153px;width:93px;background:linear-gradient(var(--blue-light),var(--blue-dark))">Seasonal Rates</div>
<div class="abs panel"></div>

<div class="abs villa" style="left:73px"><div class="photo" role="img" aria-label="Modern villa at dusk" style="background:linear-gradient(180deg,#2f5a9a,#c7803c 60%,#1b3666)"></div><h4>Lorem Ipsum is simply</h4><div class="pin"><svg width="5" height="7" viewBox="0 0 10 14"><path d="M5 0a5 5 0 00-5 5c0 4 5 9 5 9s5-5 5-9a5 5 0 00-5-5z" fill="#777"/></svg>lorem ipsum</div></div>
<div class="abs villa" style="left:189px"><div class="photo" role="img" aria-label="Villa lit at night" style="background:linear-gradient(180deg,#1e2a44,#b07a3e 55%,#2a2a2a)"></div><h4>Lorem Ipsum is simply</h4><div class="pin"><svg width="5" height="7" viewBox="0 0 10 14"><path d="M5 0a5 5 0 00-5 5c0 4 5 9 5 9s5-5 5-9a5 5 0 00-5-5z" fill="#777"/></svg>lorem ipsum</div></div>
<div class="abs villa" style="left:304px"><div class="photo" role="img" aria-label="Villa pool at twilight" style="background:linear-gradient(180deg,#8a9bb8,#4a5a6a 55%,#1e3a5a)"></div><h4>Lorem Ipsum is simply</h4><div class="pin"><svg width="5" height="7" viewBox="0 0 10 14"><path d="M5 0a5 5 0 00-5 5c0 4 5 9 5 9s5-5 5-9a5 5 0 00-5-5z" fill="#777"/></svg>lorem ipsum</div></div>
<div class="abs villa" style="left:419px"><div class="photo" role="img" aria-label="Thatched terrace by the sea" style="background:linear-gradient(180deg,#6aa0d8,#9a7a5a 50%,#2e6a8a)"></div><h4>Lorem Ipsum is simply</h4><div class="pin"><svg width="5" height="7" viewBox="0 0 10 14"><path d="M5 0a5 5 0 00-5 5c0 4 5 9 5 9s5-5 5-9a5 5 0 00-5-5z" fill="#777"/></svg>lorem ipsum</div></div>
<div class="abs villa" style="left:534px"><div class="photo" role="img" aria-label="Palm-shaded villa by the sea" style="background:linear-gradient(135deg,#2a4a2a,#4a8ac8 55%,#1a5a8a)"></div><h4>Lorem Ipsum is simply</h4><div class="pin"><svg width="5" height="7" viewBox="0 0 10 14"><path d="M5 0a5 5 0 00-5 5c0 4 5 9 5 9s5-5 5-9a5 5 0 00-5-5z" fill="#777"/></svg>lorem ipsum</div></div>

<footer class="abs footer"></footer>
<div class="abs fcol" style="left:74px"><h5>WELCOME</h5><ul><li>Home</li><li>About Us</li><li>Services</li><li>Villas</li><li>Videos</li><li>Gallery</li><li>News</li><li>Contact us</li></ul></div>
<div class="abs fcol" style="left:171px"><h5>INFORMATION</h5><ul><li>Terms &amp; Conditions</li><li>Privacy policy</li><li>Disclaimer</li><li>Sitemap</li></ul></div>
<div class="abs fcol" style="left:289px"><h5>CONTACT INFO</h5><ul>
  <li class="strong">Palm Cove Villas in Phuket</li>
  <li>48 Palm Lane, Beach Town,</li>
  <li>Country name : 2365233</li>
  <li><svg width="6" height="6" viewBox="0 0 24 24"><path fill="#555" d="M6.6 10.8a15 15 0 006.6 6.6l2.2-2.2c.3-.3.7-.4 1-.2 1.1.4 2.3.6 3.6.6.6 0 1 .4 1 1V20c0 .6-.4 1-1 1A17 17 0 013 4c0-.6.4-1 1-1h3.5c.6 0 1 .4 1 1 0 1.3.2 2.5.6 3.6.1.3 0 .7-.2 1z"/></svg>&nbsp; (3652) 410 872</li>
  <li><svg width="6" height="5" viewBox="0 0 24 18"><rect width="24" height="18" fill="#555"/></svg>&nbsp; info@palmcovevillas.com</li>
</ul></div>
<div class="abs fcol social" style="left:451px"><h5>FOLLOW US</h5><ul>
  <li><i style="background:#2b4f8f"></i>: Friendly</li>
  <li><i style="background:#2aa3d8"></i>: Chirpline</li>
  <li><i style="background:#1d6a94"></i>: WorkNet</li>
  <li><i style="background:#d42027"></i>: Pinboard</li>
</ul></div>
<div class="abs flogo">Palm Cove Villas</div>
<div class="abs copy">© 2015. Palm Cove Villas. All Rights Reserved.</div>
</body>
</html>
```